need corporate, modern business card created for Consulting Company

I need a slick business card using elements from my website, as well as, integrating my pixelforge-created logo (see files).

The business card needs to be:
1. Corporate and modern
2. Clean and professional

I've included a PSD with the logo/icon that you can use to create it. Feel free to try a metallic finish on the logo, make it bigger/small, underlay it. Whatever you need to do to make my card stand out.

Try a black background, or white background or gray.

The idea is for my card to be memorable as well as professional and corporate.

Target Market(s)

Corporate business in the US and Canada.

Industry/Entity Type

Business

Contact Information for Business Card

Commerce Advancing Methods
Martin Coles, Senior Partner
office: 1 877 555 0143
mobile: 1 519 555 0172
website: http://www.brightvale.example

Requirements
Must have
• Card-related information
• corporate, yet modern
• clean and professional
• incorporate the icon only
• must have an editable form when complete!
Nice to have
• metallic icon might be cool
• try it with white or black

```html
<!DOCTYPE html>
<html lang="en">
<head>
<meta charset="utf-8">
<title>Brightvale Business Card</title>
<link href="https://fonts.googleapis.com/css2?family=Open+Sans:wght@400;600;700;800&display=swap" rel="stylesheet">
<style>
  :root {
    --page-bg: #e9e9ea;
    --card-white: #ffffff;
    --brand-blue: #3d8fd6;
    --brand-blue-light: #5aa7e4;
    --brand-blue-deep: #2f78c0;
    --ink: #2b2b2e;
    --text-on-blue: #ffffff;
    --shadow: rgba(0, 0, 0, 0.18);
  }
  * { box-sizing: border-box; margin: 0; padding: 0; }
  html, body { width: 1200px; height: 885px; overflow: hidden; }
  body {
    background: var(--page-bg);
    font-family: "Open Sans", Arial, sans-serif;
    position: relative;
  }
  .card {
    position: absolute;
    width: 530px;
    height: 303px;
    background: var(--card-white);
    box-shadow: 0 10px 30px var(--shadow);
    overflow: hidden;
  }
  .card--front { left: 45px; top: 291px; }
  .card--back { left: 625px; top: 291px; }

  /* Front */
  .front__artwork {
    position: absolute;
    right: 0; top: 0;
    width: 200px; height: 132px;
    background: linear-gradient(135deg, var(--brand-blue-light), var(--brand-blue));
    clip-path: polygon(30% 100%, 18% 55%, 40% 30%, 55% 0, 100% 0, 100% 100%);
  }
  .front__band {
    position: absolute;
    left: 46px; right: 0; top: 130px; bottom: 0;
    background: linear-gradient(160deg, var(--brand-blue-light), var(--brand-blue-deep));
  }
  .brand {
    display: flex;
    align-items: center;
    gap: 10px;
  }
  .brand__mark {
    width: 22px; height: 22px;
    background: var(--brand-blue);
  }
  .brand__name {
    font-weight: 800;
    color: var(--ink);
    letter-spacing: -0.5px;
    line-height: 1;
  }
  .front__brand { position: absolute; left: 30px; top: 40px; }
  .front__brand .brand__name { font-size: 44px; }
  .front__tagline {
    position: absolute;
    left: 64px; top: 98px;
    font-size: 13px;
    font-weight: 600;
    color: var(--ink);
  }
  .contact {
    position: absolute;
    left: 82px; top: 158px;
    color: var(--text-on-blue);
  }
  .contact__title {
    font-size: 21px;
    font-weight: 700;
    margin-bottom: 10px;
    white-space: nowrap;
  }
  .contact__role {
    font-weight: 400;
    font-size: 16px;
    padding-left: 8px;
    margin-left: 6px;
    border-left: 1px solid rgba(255,255,255,0.7);
  }
  .contact__list { list-style: none; }
  .contact__item {
    display: flex;
    align-items: center;
    gap: 9px;
    font-size: 13px;
    line-height: 22px;
  }
  .contact__icon { width: 14px; height: 14px; }

  /* Back */
  .back__pattern {
    position: absolute;
    left: 0; right: 0;
    height: 96px;
    background: repeating-linear-gradient(90deg, var(--brand-blue) 0 26px, var(--brand-blue-light) 26px 40px);
  }
  .back__pattern--top { top: 0; }
  .back__pattern--bottom { bottom: 0; }
  .back__brand {
    position: absolute;
    left: 0; right: 0; top: 96px; bottom: 96px;
    justify-content: center;
  }
  .back__brand .brand__name { font-size: 50px; }
</style>
</head>
<body>
  <section class="card card--front" aria-label="Business card front">
    <div class="front__artwork" role="img" aria-label="Large blue brand graphic of flowing connected strands"></div>
    <div class="brand front__brand">
      <span class="brand__mark"></span>
      <span class="brand__name">brightvale</span>
    </div>
    <p class="front__tagline">Commerce Advancing Methods</p>
    <div class="front__band"></div>
    <div class="contact">
      <p class="contact__title">Martin Coles<span class="contact__role">Senior Partner</span></p>
      <ul class="contact__list">
        <li class="contact__item">
          <svg class="contact__icon" viewBox="0 0 24 24" fill="#fff"><path d="M6.6 10.8a15.1 15.1 0 0 0 6.6 6.6l2.2-2.2c.3-.3.7-.4 1-.2 1.1.4 2.3.6 3.6.6.6 0 1 .4 1 1V20c0 .6-.4 1-1 1A17 17 0 0 1 3 4c0-.6.4-1 1-1h3.5c.6 0 1 .4 1 1 0 1.3.2 2.5.6 3.6.1.3 0 .7-.2 1z"/></svg>
          <span>1 877 555 0143</span>
        </li>
        <li class="contact__item">
          <svg class="contact__icon" viewBox="0 0 24 24" fill="none" stroke="#fff" stroke-width="2.2"><rect x="6" y="2" width="12" height="20" rx="2"/><line x1="10" y1="18" x2="14" y2="18"/></svg>
          <span>1 519 555 0172</span>
        </li>
        <li class="contact__item">
          <svg class="contact__icon" viewBox="0 0 24 24" fill="none" stroke="#fff" stroke-width="2"><circle cx="12" cy="12" r="10"/><path d="M2 12h20M12 2c3 3 3 17 0 20M12 2c-3 3-3 17 0 20"/></svg>
          <span>www.brightvale.example</span>
        </li>
      </ul>
    </div>
  </section>

  <section class="card card--back" aria-label="Business card back">
    <div class="back__pattern back__pattern--top" role="img" aria-label="Blue and white wave pattern band"></div>
    <div class="brand back__brand">
      <span class="brand__mark"></span>
      <span class="brand__name">brightvale</span>
    </div>
    <div class="back__pattern back__pattern--bottom" role="img" aria-label="Blue and white wave pattern band"></div>
  </section>
</body>
</html>
```